WordPress website design for wealth management company

A modern clean look website for a service company. This is mostly for information only, with a form to capture prospect contact information and schedule a 15 minutes call. There will be several static pages describe what services we offer, how we are different, and a blog section for posting articles and share resources. A section for client testimonials.
I want a website that is easy to understand and maintain. No proprietary plugins that cost extra. The main thing I need help is the visual layout / color palette that present a clean and professional look, select the suitable stock photos that convey the image of trust, professional, innovative, and high service.
Some websites with style I like include the following
- https://www.halvorbrook.com/
- https://www.trivanplanningworks.com/
- https://morvellfunds.com/private-equity-partners/
Also some websites in other industries with clean modern look
- https://zentrell.com/
- https://quovra.com/
- https://www.plumtorvik.com/
I want the end product to be a fully functional website that I can upload into web hosting service I use and I can easily add content and maintain myself in the future.

```html
<!DOCTYPE html>
<html lang="en">
<head>
<meta charset="utf-8">
<title>Marrowfield Wealth</title>
<link href="https://fonts.googleapis.com/css2?family=Libre+Baskerville:wght@400;700&family=Poppins:wght@400;500;600&display=swap" rel="stylesheet">
<style>
:root{
  --purple:#5b2a86;
  --gold:#f9bf3b;
  --ink:#2b2b2b;
  --body:#3c3c3c;
  --muted:#f3f3f4;
  --line:#cfcfd4;
  --footer:#2c2c2c;
  --footer-text:#d8d8d8;
  --serif:'Libre Baskerville', Georgia, serif;
  --sans:'Poppins', Arial, sans-serif;
}
*{box-sizing:border-box;margin:0;padding:0}
html,body{width:1200px;height:4589px;overflow:hidden}
body{position:relative;font-family:var(--sans);color:var(--body);background:#fff}
.abs{position:absolute}
.topbar{left:0;top:0;width:1200px;height:59px;background:#f4f4f5}
.topbar .contact{position:absolute;top:20px;font-family:var(--serif);font-size:15px;color:var(--purple);display:flex;align-items:center;gap:10px;white-space:nowrap}
.header{left:0;top:59px;width:1200px;height:101px;background:#fff}
.brand{position:absolute;left:75px;top:28px;display:flex;align-items:center;gap:12px}
.brand-dot{width:40px;height:40px;border-radius:50%;background:var(--purple)}
.brand-name{font-family:var(--sans);font-weight:600;font-size:22px;letter-spacing:2px;color:var(--purple);line-height:1}
.brand-name small{display:block;font-size:11px;letter-spacing:4px;font-weight:600;margin-top:4px}
.nav{position:absolute;top:46px;right:72px;display:flex;gap:39px;font-size:14px;color:#333}
.nav .active{color:var(--purple);font-weight:600}
.hero{left:0;top:160px;width:1200px;height:629px;background:linear-gradient(90deg,#f5f5f7 0%,#ebe9ec 38%,#8a7f82 60%,#4c4148 75%,#6f8fb0 90%,#c9d3de 100%)}
.hero-text{position:absolute;left:75px;top:135px;color:var(--ink);font-family:var(--serif)}
.hero-text .small{font-size:42px;line-height:1}
.hero-text .big{font-size:92px;font-weight:700;color:var(--purple);line-height:1.05;margin-left:6px}
.hero-text .sub{font-size:34px;line-height:44px;margin-top:6px}
.btn{display:inline-flex;align-items:center;justify-content:center;background:var(--gold);color:#fff;font-family:var(--serif);font-weight:700;font-size:18px;letter-spacing:1px}
.hero .btn{position:absolute;left:75px;top:392px;width:190px;height:59px}
.title{font-family:var(--serif);font-weight:700;color:var(--purple);font-size:35px;letter-spacing:1px;white-space:nowrap}
.rule{height:2px;background:var(--gold)}
.para{font-size:16px;line-height:28px;color:var(--body)}
.card{top:1049px;width:330px;height:445px;overflow:hidden}
.card .photo{position:absolute;inset:0}
.card .caption{position:absolute;left:22px;bottom:28px;color:#fff}
.card h3{font-family:var(--serif);font-size:25px;line-height:32px;font-weight:700;letter-spacing:.5px}
.card a{display:block;margin-top:10px;font-family:var(--serif);font-weight:700;font-size:16px;color:var(--gold);text-decoration:underline}
.diff-bg{left:588px;top:1578px;width:612px;height:559px;background:var(--muted)}
.tcard{top:2331px;width:512px;height:262px;border:2px solid var(--line);border-radius:6px;background:#fff}
.tcard .avatar{position:absolute;left:20px;top:24px;width:70px;height:70px;border-radius:4px}
.tcard .name{position:absolute;left:115px;top:38px;font-weight:600;font-size:18px;color:var(--purple)}
.tcard .loc{position:absolute;left:115px;top:66px;font-size:16px;color:#444}
.tcard .quote{position:absolute;left:20px;top:120px;width:440px;font-size:15.5px;line-height:28px}
.res-bg{left:0;top:2682px;width:1200px;height:686px;background:var(--muted)}
.res{top:2923px;width:330px}
.res .photo{height:222px}
.res h3{font-family:var(--serif);font-size:20px;line-height:28px;color:var(--ink);margin-top:34px;font-weight:400}
.res a{display:block;margin-top:16px;font-family:var(--serif);font-weight:700;font-size:16px;color:var(--gold);text-decoration:underline}
.field{border:1.5px solid var(--line);background:#fff;font-size:13px;color:#666;padding:20px 14px}
.submit{left:255px;top:3932px;width:691px;height:61px;font-size:19px}
.footer{left:0;top:4082px;width:1200px;height:507px;background:var(--footer)}
.fbrand{position:absolute;left:75px;top:80px;display:flex;flex-direction:column;align-items:center;width:230px}
.fbrand .dot{width:90px;height:90px;border-radius:50%;border:8px solid #d9d9d9}
.fbrand .name{margin-top:18px;font-weight:600;font-size:28px;letter-spacing:2px;color:#e6e6e6;line-height:1;text-align:center}
.fbrand .name small{display:block;font-size:18px;letter-spacing:5px;margin-top:6px}
.fcontact{position:absolute;left:75px;font-family:var(--serif);font-size:15px;color:#fff;display:flex;align-items:center;gap:14px;white-space:nowrap}
.fcol{position:absolute;top:76px}
.fcol h4{font-family:var(--serif);font-weight:700;font-size:23px;color:var(--gold);margin-bottom:16px;letter-spacing:.5px}
.fcol li{list-style:none;font-size:15px;color:var(--footer-text);height:44.5px}
.fbottom{position:absolute;left:0;top:427px;width:1200px;height:1px;background:#444}
.copy{position:absolute;left:75px;top:462px;font-size:13px;color:#aaa}
.social{position:absolute;right:75px;top:458px;display:flex;gap:16px}
.social span{width:18px;height:18px;border-radius:50%;background:#9a9a9a}
</style>
</head>
<body>

<div class="abs topbar">
  <div class="contact" style="left:660px">
    <svg width="16" height="16" viewBox="0 0 24 24" aria-hidden="true"><path fill="#f9bf3b" d="M6.6 10.8a15 15 0 0 0 6.6 6.6l2.2-2.2c.3-.3.7-.4 1-.2 1.1.4 2.3.6 3.6.6.6 0 1 .4 1 1V20c0 .6-.4 1-1 1A17 17 0 0 1 3 4c0-.6.4-1 1-1h3.5c.6 0 1 .4 1 1 0 1.3.2 2.5.6 3.6.1.3 0 .7-.2 1z"/></svg>
    +1-555-014-2880
  </div>
  <div class="contact" style="left:850px">
    <svg width="18" height="14" viewBox="0 0 24 18" aria-hidden="true"><rect width="24" height="18" rx="2" fill="#f9bf3b"/><path d="M1 2l11 8 11-8" stroke="#fff" stroke-width="2" fill="none"/></svg>
    hello@marrowfieldwealth.com
  </div>
</div>

<header class="abs header">
  <div class="brand">
    <div class="brand-dot"></div>
    <div class="brand-name">MARROWFIELD<small>WEALTH</small></div>
  </div>
  <nav class="nav">
    <span class="active">Home</span><span>Services We Offer</span><span>How We Are Different</span><span>Blog</span><span>Testimonials</span><span>Contact Us</span>
  </nav>
</header>

<section class="abs hero" role="img" aria-label="Smiling advisor in a suit and a nurse in blue scrubs holding a clipboard in a bright clinic">
  <div class="hero-text">
    <div class="small">Welcome to</div>
    <div class="big">Marrowfield</div>
    <div class="sub">We are a health<br>management company.</div>
  </div>
  <span class="btn">Learn More</span>
</section>

<h2 class="abs title" style="left:75px;top:862px">What Services We Offer</h2>
<div class="abs rule" style="left:75px;top:921px;width:345px"></div>
<p class="abs para" style="left:75px;top:948px;width:1020px">Sed ut perspiciatis unde omnis iste natus error sit voluptatem accusantium doloremque laudantium, totam rem aperiam, eaque ipsa quae ab illo inventore veritatis et quasi architecto beatae vitae dicta sunt explicabo.</p>

<div class="abs card" style="left:75px">
  <div class="photo" role="img" aria-label="Senior doctor with a tablet beside a colleague" style="background:linear-gradient(180deg,#d9dde2 0%,#9aa7b5 45%,#3a3f48 75%,#111 100%)"></div>
  <div class="caption"><h3>Nemo enimipsam<br>voluptatem</h3><a>Read More</a></div>
</div>
<div class="abs card" style="left:436px">
  <div class="photo" role="img" aria-label="Smiling older couple sitting together" style="background:linear-gradient(180deg,#a89a88 0%,#8a6f5c 45%,#3d3029 75%,#111 100%)"></div>
  <div class="caption"><h3>Nemo enimipsam<br>voluptatem</h3><a>Read More</a></div>
</div>
<div class="abs card" style="left:798px">
  <div class="photo" role="img" aria-label="Doctor in a suit holding a tablet in a hospital corridor" style="background:linear-gradient(180deg,#eceef0 0%,#b9bcc1 45%,#44464b 75%,#111 100%)"></div>
  <div class="caption"><h3>Nemo enimipsam<br>voluptatem</h3><a>Read More</a></div>
</div>

<div class="abs" role="img" aria-label="Nurse in blue scrubs smiling with a clipboard" style="left:0;top:1578px;width:294px;height:559px;background:linear-gradient(135deg,#e9dbd0,#c99d86 40%,#5b8ab5 70%,#2f5f8c)"></div>
<div class="abs" role="img" aria-label="Doctor consulting with a client at a desk" style="left:294px;top:1578px;width:294px;height:280px;background:linear-gradient(135deg,#f0eeea,#c9c4bc 55%,#6d6b6e)"></div>
<div class="abs" role="img" aria-label="Older couple smiling while reading documents" style="left:294px;top:1858px;width:294px;height:279px;background:linear-gradient(135deg,#b6a08c,#d8c7b6 45%,#7e6f66)"></div>
<div class="abs diff-bg"></div>
<h2 class="abs title" style="left:616px;top:1630px">How We Are Different</h2>
<div class="abs rule" style="left:616px;top:1688px;width:340px"></div>
<p class="abs para" style="left:616px;top:1715px;width:520px;font-size:15.5px">Sed ut perspiciatis unde omnis iste natus error sit voluptatem accusantium doloremque laudantium, totam rem aperiam, eaque ipsa quae ab illo inventore veritatis et quasi architecto beatae vitae dicta sunt explicabo.</p>
<p class="abs para" style="left:616px;top:1843px;width:520px;font-size:15.5px">Nemo enim ipsam voluptatem quia voluptas sit aspernatur aut odit aut fugit, sed quia consequuntur magni dolores eos qui ratione voluptatem sequi nesciunt. Neque porro quisquam est, qui dolorem ipsum quia dolor sit amet, consectetur.</p>
<span class="abs btn" style="left:616px;top:2018px;width:191px;height:59px">Learn More</span>

<h2 class="abs title" style="left:0;top:2214px;width:1200px;text-align:center">Client Testimonials</h2>
<div class="abs rule" style="left:406px;top:2273px;width:366px"></div>

<svg class="abs" style="left:37px;top:2452px" width="23" height="23" viewBox="0 0 24 24" aria-hidden="true"><circle cx="12" cy="12" r="10" fill="none" stroke="#444" stroke-width="2"/><path d="M15 12H8m3-3-3 3 3 3" stroke="#444" stroke-width="2" fill="none"/></svg>
<svg class="abs" style="left:1141px;top:2452px" width="23" height="23" viewBox="0 0 24 24" aria-hidden="true"><circle cx="12" cy="12" r="10" fill="none" stroke="#f9bf3b" stroke-width="2"/><path d="M8 12h7m-3-3 3 3-3 3" stroke="#f9bf3b" stroke-width="2" fill="none"/></svg>

<div class="abs tcard" style="left:75px">
  <div class="avatar" role="img" aria-label="Portrait of a client" style="background:linear-gradient(135deg,#d7d2cc,#7d7570)"></div>
  <div class="name">Name Heading</div><div class="loc">Location</div>
  <p class="quote">“ Nemo enim ipsam voluptatem quia voluptas sit aspernatur aut odit aut fugit, sed quia consequuntur magni dolores eos qui ratione voluptatem sequi que porro quisquam est, qui dolore..”</p>
</div>
<div class="abs tcard" style="left:614px">
  <div class="avatar" role="img" aria-label="Portrait of a client" style="background:linear-gradient(135deg,#e9e4df,#a0826c)"></div>
  <div class="name">Name Heading</div><div class="loc">Location</div>
  <p class="quote">“ Nemo enim ipsam voluptatem quia voluptas sit aspernatur aut odit aut fugit, sed quia consequuntur magni dolores eos qui ratione voluptatem sequi que porro quisquam est, qui dolore..”</p>
</div>

<div class="abs res-bg"></div>
<h2 class="abs title" style="left:75px;top:2737px">Resources</h2>
<div class="abs rule" style="left:75px;top:2797px;width:152px"></div>
<p class="abs para" style="left:75px;top:2823px;width:1020px">Sed ut perspiciatis unde omnis iste natus error sit voluptatem accusantium doloremque laudantium, totam rem aperiam, eaque ipsa quae ab illo inventore veritatis et quasi architecto beatae vitae dicta sunt explicabo.</p>

<div class="abs res" style="left:75px">
  <div class="photo" role="img" aria-label="Advisor meeting a couple at a laptop" style="background:linear-gradient(135deg,#efefef,#b9b3ad 55%,#4b4440)"></div>
  <h3>Nemo enim ipsam volupt atem quia voluptas dicta sunt explicabo..</h3><a>Read More</a>
</div>
<div class="abs res" style="left:436px">
  <div class="photo" role="img" aria-label="Older couple talking with an advisor" style="background:linear-gradient(135deg,#b8a999,#8a6e5c 50%,#554a46)"></div>
  <h3>Nemo enim ipsam volupt atem quia voluptas dicta sunt explicabo..</h3><a>Read More</a>
</div>
<div class="abs res" style="left:798px">
  <div class="photo" role="img" aria-label="Doctor presenting to a seated audience" style="background:linear-gradient(135deg,#f1f3f5,#c6ccd3 50%,#3f4f62)"></div>
  <h3>Nemo enim ipsam volupt atem quia voluptas dicta sunt explicabo..</h3><a>Read More</a>
</div>

<h2 class="abs title" style="left:0;top:3434px;width:1200px;text-align:center">Schedule a 15 Minutes Call</h2>
<p class="abs para" style="left:100px;top:3519px;width:1000px;text-align:center">Sed ut perspiciatis unde omnis iste natus error sit voluptatem accusantium doloremque laudantium, totam rem aperiam, eaque ipsa quae ab illo inventore veritatis et quasi architecto beatae vitae dicta sunt explicabo.</p>
<div class="abs field" style="left:255px;top:3619px;width:331px;height:61px">Name</div>
<div class="abs field" style="left:614px;top:3619px;width:332px;height:61px">Phone No</div>
<div class="abs field" style="left:255px;top:3697px;width:691px;height:61px">Email Address</div>
<div class="abs field" style="left:255px;top:3774px;width:691px;height:144px">Message</div>
<span class="abs btn submit">Submit Now</span>

<footer class="abs footer">
  <div class="fbrand">
    <div class="dot"></div>
    <div class="name">MARROWFIELD<small>WEALTH</small></div>
  </div>
  <div class="fcontact" style="top:284px">
    <svg width="16" height="16" viewBox="0 0 24 24" aria-hidden="true"><path fill="#f9bf3b" d="M6.6 10.8a15 15 0 0 0 6.6 6.6l2.2-2.2c.3-.3.7-.4 1-.2 1.1.4 2.3.6 3.6.6.6 0 1 .4 1 1V20c0 .6-.4 1-1 1A17 17 0 0 1 3 4c0-.6.4-1 1-1h3.5c.6 0 1 .4 1 1 0 1.3.2 2.5.6 3.6.1.3 0 .7-.2 1z"/></svg>
    +1-555-014-2880
  </div>
  <div class="fcontact" style="top:319px">
    <svg width="18" height="14" viewBox="0 0 24 18" aria-hidden="true"><rect width="24" height="18" rx="2" fill="#f9bf3b"/><path d="M1 2l11 8 11-8" stroke="#2c2c2c" stroke-width="2" fill="none"/></svg>
    hello@marrowfieldwealth.com
  </div>
  <div class="fcol" style="left:404px"><h4>Site Map</h4><ul><li>Services We Offer</li><li>How We Are Different</li><li>Blog</li><li>Testimonials</li><li>Contact Us</li></ul></div>
  <div class="fcol" style="left:654px"><h4>Services</h4><ul><li>Nemo Enim Ipsam</li><li>Voluptatem Quia</li><li>Voluptas Sit Aspernatur</li><li>Aut Odit Aut Fugit</li><li>Sed Quia</li></ul></div>
  <div class="fcol" style="left:914px"><h4>Resources</h4><ul><li>Nemo Enim Ipsam</li><li>Voluptatem Quia</li><li>Voluptas Sit Aspernatur</li><li>Aut Odit Aut Fugit</li><li>Sed Quia</li></ul></div>
  <div class="fbottom"></div>
  <div class="copy">Copyright © 2023. Marrowfield Wealth. All Right Reserved</div>
  <div class="social" aria-label="Social links"><span></span><span></span><span></span><span></span><span></span></div>
</footer>

</body>
</html>
```